New Candy Packaging Design

Looking to create an attractive design for modern retail for our single stick candy that will stand out on retail shelves. It will be hung from a whole. The design should have brand elements like the irregular shapes, bright pastel colors. Please visit plumcrestcandyworks.com to ensure the product could be an extension of the product range. 3 colors, pink(sakura flavor), green(muscat grape flavor), and blue(french vanilla flavor).

Target Market(s)

Millenias and Genz

Industry/Entity Type

Food

Requirements
Must have
• Look and feel of brand extension for Tindra, Matt finish
Nice to have
• fruit shapes
Should not have
• tacky design

```html
<!DOCTYPE html>
<html lang="en">
<head>
<meta charset="UTF-8">
<title>Tindra Rock Sugar Sticks – Package Front</title>
<link rel="stylesheet" href="https://fonts.googleapis.com/css2?family=Crimson+Text:wght@400;600&display=swap">
<style>
  :root {
    --backdrop: #f3dbe8;
    --pack-white: #ffffff;
    --pack-shade: #e9e9ec;
    --brand-pink: #e0519a;
    --brand-red: #c8243a;
    --hole: #2a2a2e;
    --callout-ink: #333333;
  }
  * { margin: 0; padding: 0; box-sizing: border-box; }
  html, body {
    width: 1200px;
    height: 2284px;
    overflow: hidden;
    background: var(--backdrop);
  }
  .canvas {
    position: relative;
    width: 1200px;
    height: 2284px;
  }
  .package {
    position: absolute;
    left: 120px;
    top: 52px;
    width: 960px;
    height: 2180px;
    background: linear-gradient(90deg, var(--pack-shade) 0%, var(--pack-white) 8%, var(--pack-white) 92%, var(--pack-shade) 100%);
    border-radius: 18px;
    overflow: hidden;
    box-shadow: 0 24px 40px rgba(120, 60, 90, 0.18);
  }
  .crimp {
    position: absolute;
    left: 0;
    width: 100%;
    height: 120px;
    background: repeating-linear-gradient(90deg, rgba(0,0,0,0.025) 0 6px, transparent 6px 14px);
  }
  .crimp--top { top: 0; border-bottom: 2px solid rgba(0,0,0,0.05); }
  .crimp--bottom { bottom: 0; border-top: 2px solid rgba(0,0,0,0.05); }
  .hang-hole {
    position: absolute;
    top: 58px;
    left: 50%;
    width: 44px;
    height: 44px;
    margin-left: -22px;
    border-radius: 50%;
    background: var(--hole);
  }
  .label {
    position: absolute;
    top: 165px;
    left: 50px;
    width: 860px;
    height: 225px;
    border: 8px solid var(--brand-pink);
    border-radius: 110px / 60px;
    background: var(--pack-white);
    text-align: center;
    font-family: "Crimson Text", serif;
  }
  .label__line {
    margin-top: 18px;
    font-size: 42px;
    font-weight: 400;
    color: var(--brand-red);
    letter-spacing: 1px;
  }
  .label__name {
    font-size: 128px;
    line-height: 1;
    font-weight: 600;
    color: var(--brand-pink);
  }
  .artwork {
    position: absolute;
    top: 400px;
    left: 0;
    width: 100%;
    height: 1520px;
    background: linear-gradient(160deg, #e8333a 0%, #f28a2a 18%, #f6d23a 34%, #48b85a 52%, #2f8fd6 70%, #5a3fa8 86%, #b23c8e 100%);
  }
  .candy-window {
    position: absolute;
    top: 580px;
    left: 370px;
    width: 200px;
    height: 1180px;
    border-radius: 90px 90px 100px 100px;
    background: linear-gradient(180deg, #d8a66a 0%, #c48a4f 45%, #e8d2b0 62%, #f2e6cf 100%);
    opacity: 0.95;
  }
  .callout {
    position: absolute;
    top: 540px;
    left: 680px;
    width: 220px;
    padding: 10px 12px;
    background: var(--pack-white);
    border: 2px solid var(--callout-ink);
    font-family: "Crimson Text", serif;
    font-size: 26px;
    line-height: 1.15;
    text-align: center;
    color: var(--callout-ink);
  }
  .callout-line {
    position: absolute;
    top: 0;
    left: 0;
  }
  .maker-name {
    position: absolute;
    top: 1955px;
    width: 100%;
    text-align: center;
    font-family: "Crimson Text", serif;
    font-size: 66px;
    font-weight: 400;
    color: var(--brand-red);
  }
</style>
</head>
<body>
<div class="canvas">
  <div class="package">
    <div class="crimp crimp--top"></div>
    <div class="hang-hole"></div>

    <div class="label">
      <p class="label__line">Rock Sugar Sticks</p>
      <p class="label__name">Tindra</p>
    </div>

    <div class="artwork" role="img" aria-label="Bright faceted polygon pattern in rainbow colours"></div>

    <div class="candy-window" role="img" aria-label="Clear window showing an amber rock sugar crystal stick"></div>

    <svg class="callout-line" width="960" height="2180" aria-hidden="true">
      <line x1="680" y1="585" x2="520" y2="660" stroke="#333333" stroke-width="2"/>
      <circle cx="520" cy="660" r="5" fill="#333333"/>
    </svg>
    <div class="callout">Clear Window<br>Transparent</div>

    <p class="maker-name">Marlow Sweets Co</p>
    <div class="crimp crimp--bottom"></div>
  </div>
</div>
</body>
</html>
```